Shampoo and Shower Gel Packaging Design

I need a new packaging design for a men shampoo and shower gel bottle. The packaging must me black (black bottle/package) and the logo should be also monochrom.
For example, black matte bottle and black shiny logo on the packaging (not mandatory).
the design must contain maximum 3 colors.
1. black
2. white (text)
3. grey/dark blue/dark green (colors will be the difference between products parfumes/smell/scences.

Design must be minimalist/elegant/discrete.
Updates

Please check the photos i added for pure inspiration.

Target Market(s)

brand exclusively for MEN - premium clients

Industry/Entity Type

Cosmetics

Font styles to use
Sans Serif

Colors
1b1b1b
5c5c5c
aaaaaa
ffffff
3176b5

Requirements
Must have
• black background
• minimalist design

```html
<!DOCTYPE html>
<html lang="en">
<head>
<meta charset="utf-8">
<title>Orvel Cosmetics – Shampoo Label</title>
<link rel="stylesheet" href="https://fonts.googleapis.com/css2?family=Roboto:wght@300;400&display=swap">
<style>
  :root {
    --canvas-bg: #ffffff;
    --label-black: #0e0e0e;
    --pattern-tone: #1b1b1b;
    --text-white: #ffffff;
    --text-soft: #aaaaaa;
  }
  html, body {
    margin: 0;
    padding: 0;
    width: 1200px;
    height: 1200px;
    overflow: hidden;
    background: var(--canvas-bg);
  }
  .canvas {
    position: relative;
    width: 1200px;
    height: 1200px;
    font-family: "Roboto", sans-serif;
  }
  .label {
    position: absolute;
    left: 300px;
    top: 290px;
    width: 600px;
    height: 620px;
    background: var(--label-black);
    color: var(--text-white);
    text-align: center;
  }
  .label-pattern {
    position: absolute;
    inset: 0;
    width: 100%;
    height: 100%;
  }
  .brand {
    position: absolute;
    left: 0;
    right: 0;
    top: 48px;
  }
  .brand-dot {
    display: block;
    width: 26px;
    height: 26px;
    margin: 0 auto 18px;
    border-radius: 50%;
    background: var(--text-white);
  }
  .brand-name {
    margin: 0;
    font-weight: 300;
    font-size: 44px;
    letter-spacing: 0.42em;
    padding-left: 0.42em;
    line-height: 1;
  }
  .brand-tagline {
    margin: 12px 0 0;
    font-weight: 300;
    font-size: 10px;
    letter-spacing: 0.45em;
    padding-left: 0.45em;
  }
  .product {
    position: absolute;
    left: 0;
    right: 0;
    top: 252px;
  }
  .product-name {
    margin: 0;
    font-weight: 300;
    font-size: 46px;
    letter-spacing: 0.1em;
    line-height: 1;
  }
  .product-note {
    margin: 20px 0 0;
    font-weight: 300;
    font-size: 21px;
    letter-spacing: 0.1em;
    color: var(--text-soft);
  }
  .volume {
    position: absolute;
    left: 0;
    right: 0;
    top: 524px;
    margin: 0;
    font-weight: 300;
    font-size: 15px;
    letter-spacing: 0.08em;
    color: var(--text-soft);
  }
</style>
</head>
<body>
<main class="canvas">
  <section class="label">
    <svg class="label-pattern" viewBox="0 0 600 620" role="img" aria-label="Dark floral vine pattern covering the label background">
      <defs>
        <radialGradient id="patternTone" cx="50%" cy="50%" r="70%">
          <stop offset="0%" stop-color="#1b1b1b"/>
          <stop offset="100%" stop-color="#111111"/>
        </radialGradient>
      </defs>
      <rect width="600" height="620" fill="url(#patternTone)"/>
    </svg>

    <header class="brand">
      <span class="brand-dot"></span>
      <h1 class="brand-name">ORVEL</h1>
      <p class="brand-tagline">COSMETICS</p>
    </header>

    <div class="product">
      <h2 class="product-name">SHAMPOO</h2>
      <p class="product-note">PURE ESSENTIAL OIL</p>
    </div>

    <p class="volume">200ML</p>
  </section>
</main>
</body>
</html>
```